Unique Business Card Design

Unique Business Card design for our orthotic and prosthetic company. Our logo is on our website, color is light blue. Unique shape (artificial leg shaped, vertical, etc..) preferred. Logo, business name, individual name and basic demographics needed.

Industry/Entity Type

Business

Contact Information for Business Card

Logo, Industry, Phone # Logo, "Prosthetic & Orthotic Services" Place to add individual name and contact info

Colors
cee9f5

Requirements
Must have
• The icon must be there, placement of "Prosthetic & Orthotic Services" can be moved
Nice to have
• Like the mix of light blue, and a little darker blue. One design included the icons from my website which was a nice touch

```html
<!DOCTYPE html>
<html lang="en">
<head>
<meta charset="utf-8">
<title>FormaLimb Inc. – Business Card</title>
<link rel="stylesheet" href="https://fonts.googleapis.com/css2?family=Montserrat:wght@400;500;600;700&family=Playfair+Display:ital@1&display=swap">
<style>
  :root {
    --brand-blue: #1c62b4;
    --brand-blue-deep: #174f93;
    --sky: #cee9f5;
    --sky-mid: #8fc3e6;
    --white: #ffffff;
    --backdrop: #2a2b2d;
  }
  * { box-sizing: border-box; margin: 0; padding: 0; }
  html, body { width: 1200px; height: 900px; overflow: hidden; }
  body {
    background: var(--backdrop);
    font-family: "Montserrat", sans-serif;
    display: flex; flex-direction: column; align-items: center; justify-content: center;
    gap: 40px;
  }
  .card {
    position: relative;
    width: 700px; height: 400px;
    border-radius: 26px;
    overflow: hidden;
  }
  .card svg.card-shapes { position: absolute; inset: 0; }

  /* Front */
  .card-front { background: var(--white); }
  .front-brand {
    position: absolute; left: 190px; top: 60px;
    display: flex; align-items: center; gap: 22px;
  }
  .brand-dot {
    width: 120px; height: 120px; border-radius: 50%;
    background: var(--brand-blue);
  }
  .front-brand .brand-name {
    color: var(--brand-blue); font-weight: 700; font-size: 30px; letter-spacing: 0.5px;
  }
  .service {
    position: absolute; display: flex; flex-direction: column; align-items: center; gap: 10px;
    color: var(--brand-blue); font-weight: 600; font-size: 15px; letter-spacing: 0.5px;
  }
  .service-icon {
    width: 52px; height: 52px; border-radius: 50%;
    background: radial-gradient(circle at 35% 30%, var(--white), var(--sky) 45%, var(--sky-mid));
    border: 2px solid var(--sky-mid);
  }
  .service-orthotics { left: 110px; top: 262px; }
  .service-prosthetics { left: 300px; top: 212px; }
  .service-vascular { left: 480px; top: 162px; }

  /* Back */
  .card-back { background: var(--brand-blue); color: var(--white); }
  .back-brand { position: absolute; left: 40px; top: 40px; display: flex; align-items: center; gap: 22px; }
  .back-brand .brand-dot { width: 96px; height: 96px; background: var(--white); }
  .back-brand .brand-name { font-weight: 700; font-size: 28px; letter-spacing: 0.5px; }
  .brand-tagline {
    font-family: "Playfair Display", serif; font-style: italic; font-size: 15px;
    border-top: 2px solid var(--white); padding-top: 4px; margin-top: 4px;
  }
  .holder { position: absolute; right: 40px; top: 150px; text-align: right; width: 300px; }
  .holder-name { font-weight: 700; font-size: 26px; }
  .holder-role { font-size: 15px; padding-bottom: 6px; border-bottom: 2px solid var(--white); }
  .holder-address { font-size: 15px; line-height: 1.45; margin-top: 10px; }
  .contacts {
    position: absolute; left: 40px; bottom: 36px; list-style: none;
    border-top: 2px solid var(--white); padding-top: 8px; width: 300px;
    font-size: 15px; line-height: 1.5;
  }
  .contacts li { display: flex; align-items: center; gap: 12px; }
  .contacts svg { width: 13px; height: 13px; flex: none; }
  .contacts .web strong { font-weight: 700; }
</style>
</head>
<body>

<section class="card card-front" aria-label="Card front">
  <svg class="card-shapes" viewBox="0 0 700 400" aria-hidden="true">
    <path d="M0 350 L370 350 L395 340 L395 338 L700 270 L700 400 L0 400 Z" fill="var(--brand-blue)"/>
    <path d="M370 350 L395 328 L420 334 Z" fill="var(--white)"/>
    <path d="M420 334 L700 262 L700 268 L420 340 Z" fill="var(--brand-blue-deep)"/>
  </svg>
  <div class="front-brand">
    <div class="brand-dot"></div>
    <span class="brand-name">FormaLimb Inc.</span>
  </div>
  <div class="service service-orthotics">
    <div class="service-icon" role="img" aria-label="Orthotics service icon"></div>ORTHOTICS
  </div>
  <div class="service service-prosthetics">
    <div class="service-icon" role="img" aria-label="Prosthetics service icon"></div>PROSTHETICS
  </div>
  <div class="service service-vascular">
    <div class="service-icon" role="img" aria-label="Vascular service icon"></div>VASCULAR
  </div>
</section>

<section class="card card-back" aria-label="Card back">
  <svg class="card-shapes" viewBox="0 0 700 400" aria-hidden="true">
    <path d="M0 372 L560 372 L585 330 L700 330 L700 400 L0 400 Z" fill="var(--white)"/>
  </svg>
  <div class="back-brand">
    <div class="brand-dot"></div>
    <div>
      <div class="brand-name">FORMALIMB INC.</div>
      <div class="brand-tagline">Prosthetic &amp; Orthotic Services</div>
    </div>
  </div>
  <div class="holder">
    <div class="holder-name">Maren Tolliver</div>
    <div class="holder-role">Orthotist/Prosthetist</div>
    <div class="holder-address">2290 Harbor Ave.<br>Brooklyn, NY 11235</div>
  </div>
  <ul class="contacts">
    <li><svg viewBox="0 0 12 12"><rect x="3" y="0.5" width="6" height="11" rx="1" fill="none" stroke="#fff" stroke-width="1.3"/></svg>845-555-0142</li>
    <li><svg viewBox="0 0 12 12"><path d="M2 1 L4.5 1 L5 4 L3.6 5 Q5 7.6 7 8.4 L8 7 L11 7.5 L11 10 Q6 11.5 2.5 7 Q0.5 4 2 1Z" fill="#fff"/></svg>718.555.0170</li>
    <li><svg viewBox="0 0 12 12"><rect x="1" y="4" width="10" height="6" rx="1" fill="#fff"/><rect x="3" y="1" width="6" height="3" fill="#fff"/></svg>718.555.0139</li>
    <li><svg viewBox="0 0 12 12"><rect x="0.7" y="2" width="10.6" height="8" fill="none" stroke="#fff" stroke-width="1.3"/><path d="M1 2.5 L6 6.5 L11 2.5" fill="none" stroke="#fff" stroke-width="1.3"/></svg>mtolliver@formalimbinc.com</li>
    <li class="web"><svg viewBox="0 0 12 12"><circle cx="6" cy="6" r="5.3" fill="none" stroke="#fff" stroke-width="1.2"/><path d="M0.7 6 H11.3 M6 0.7 Q2.5 6 6 11.3 M6 0.7 Q9.5 6 6 11.3" fill="none" stroke="#fff" stroke-width="1"/></svg><span>www.<strong>formalimbinc</strong>.com</span></li>
  </ul>
</section>

</body>
</html>
```